Keystone Trench Co Business Card*

Looking for a professional, clean and crisp business card

I am in the underground utilities industry and am just looking for a really impressive business card. I would like our card to be white with our symbol crisp and clear with it protruding. I also have a business partner that will require his name and info on the card once the design is set. I would like to have our website info on the card which is;
http://keystonetrenchco.example/

Contact Information for Business Card

Website, contact name, number and email

```html
<!DOCTYPE html>
<html lang="en">
<head>
<meta charset="UTF-8">
<title>Keystone Trench Co — Business Card</title>
<link href="https://fonts.googleapis.com/css2?family=Teko:wght@500&family=Quicksand:wght@500&display=swap" rel="stylesheet">
<style>
  :root {
    --page-bg: #e6e7ea;
    --card-dark: #0b0c0e;
    --card-dark-2: #1c1f24;
    --card-white: #ffffff;
    --ink: #0a0a0a;
    --brand-blue: #2f56a6;
    --text-dark: #222428;
    --logo-white: #ffffff;
  }
  * { margin: 0; padding: 0; box-sizing: border-box; }
  html, body {
    width: 1200px; height: 900px; overflow: hidden;
    background: var(--page-bg);
  }
  .canvas {
    position: relative; width: 1200px; height: 900px;
    display: flex; flex-direction: column; align-items: center;
    justify-content: center; gap: 36px;
  }
  .card {
    position: relative; width: 700px; height: 400px;
    box-shadow: 0 10px 30px rgba(0,0,0,0.18);
    overflow: hidden;
  }

  /* Front */
  .card-front { background: var(--card-dark); }
  .front-texture {
    position: absolute; inset: 0;
    background: linear-gradient(135deg, var(--card-dark-2) 0%, var(--card-dark) 55%, #121419 100%);
  }
  .brand-lockup {
    position: absolute; right: 48px; bottom: 80px;
    display: flex; align-items: center; gap: 14px;
  }
  .brand-dot {
    width: 26px; height: 26px; border-radius: 50%;
    background: var(--brand-blue);
  }
  .brand-name {
    font-family: 'Teko', sans-serif; font-weight: 500;
    font-size: 46px; line-height: 1; color: var(--logo-white);
    text-transform: uppercase; letter-spacing: 1px;
  }

  /* Back */
  .card-back { background: var(--card-white); }
  .pipe-band {
    position: absolute; left: 0; right: 0; height: 14px;
    background: var(--ink);
  }
  .pipe-band.top { top: 96px; }
  .pipe-band.bottom { top: 290px; }
  .flange {
    position: absolute; width: 14px; background: var(--ink);
  }
  .flange.left { left: 0; top: 64px; height: 46px; }
  .flange.right { right: 0; top: 226px; height: 78px; }
  .flange.right-top { right: 0; top: 96px; height: 30px; }

  .contact-row {
    position: absolute; left: 80px; right: 40px; top: 110px; height: 180px;
    display: flex; align-items: center;
  }
  .person-name {
    font-family: 'Teko', sans-serif; font-weight: 500;
    font-size: 40px; color: var(--brand-blue);
    text-transform: uppercase; letter-spacing: 1px;
    padding-right: 24px; white-space: nowrap;
  }
  .divider {
    width: 2px; height: 74px; background: var(--brand-blue);
    margin-right: 22px;
  }
  .contact-list { list-style: none; }
  .contact-list li {
    display: flex; align-items: center; gap: 10px;
    font-family: 'Quicksand', sans-serif; font-weight: 500;
    font-size: 17px; color: var(--text-dark); line-height: 26px;
  }
  .contact-list svg { width: 17px; height: 17px; flex: none; }
  .web-domain { color: var(--brand-blue); }
</style>
</head>
<body>
<main class="canvas">
  <section class="card card-front" aria-label="Card front">
    <div class="front-texture" role="img" aria-label="Dark diagonal pattern of pipe sections"></div>
    <div class="brand-lockup">
      <span class="brand-dot"></span>
      <span class="brand-name">Keystone Trench Co</span>
    </div>
  </section>

  <section class="card card-back" aria-label="Card back">
    <div class="pipe-band top"></div>
    <div class="pipe-band bottom"></div>
    <div class="flange left"></div>
    <div class="flange right-top"></div>
    <div class="flange right"></div>

    <div class="contact-row">
      <h1 class="person-name">Dale Whitmore</h1>
      <div class="divider"></div>
      <ul class="contact-list">
        <li>
          <svg viewBox="0 0 24 24" fill="none" stroke="#2f56a6" stroke-width="1.8"><circle cx="12" cy="12" r="10"/><path d="M8.5 7.5l2 2-1 1.5c.8 1.6 2 2.8 3.5 3.5l1.5-1 2 2-1.2 1.5c-3.8-.6-7.2-4-7.8-7.8z"/></svg>
          555-014-2286
        </li>
        <li>
          <svg viewBox="0 0 24 24" fill="none" stroke="#2f56a6" stroke-width="1.8"><rect x="2.5" y="5" width="19" height="14" rx="1"/><path d="M2.5 6l9.5 7 9.5-7"/></svg>
          Dale@keystonetrenchco.example
        </li>
        <li>
          <svg viewBox="0 0 24 24" fill="none" stroke="#2f56a6" stroke-width="1.8"><circle cx="12" cy="12" r="10"/><path d="M2 12h20M12 2c3 3 3 17 0 20M12 2c-3 3-3 17 0 20"/></svg>
          <span>www.<span class="web-domain">keystonetrenchco</span>.example</span>
        </li>
      </ul>
    </div>
  </section>
</main>
</body>
</html>
```